Salon and Spa Distributor Business Card

Need a business card. We are are distributor in the salon and spa industry. We identify with natural beauty. Need a card with:
Company Name: Petal Quarry"
Title: "President & CEO"
Address
Company Phone number
email
website
Tag Line:" The Professional Salon Source"

Industry/Entity Type

Business

Contact Information for Business Card

Name: Dov Strommen
Title: "President & CEO"
Address: 31 Harlow Ln, Bexmoor, NJ 07813
Company Phone number: 800-463-5918
email: dovstrommen@petalquarry.example
website: www.petalquarry.example

Requirements
Should not have
• No black backgrounds

```html
<!DOCTYPE html>
<html lang="en">
<head>
<meta charset="utf-8">
<title>Petal Quarry Business Card</title>
<link rel="stylesheet" href="https://fonts.googleapis.com/css2?family=Didact+Gothic&display=swap">
<style>
  :root {
    --backdrop: #e7e3df;
    --card-white: #ffffff;
    --card-back: #1f5a30;
    --back-ink: #cfe6d3;
    --back-ink-soft: #9cc7a5;
    --brand-green: #1f8a3a;
    --leaf-green: #3fb34f;
    --ink: #2b2b2b;
    --ink-soft: #555555;
  }
  * { box-sizing: border-box; margin: 0; padding: 0; }
  html, body {
    width: 1200px; height: 716px; overflow: hidden;
    background: var(--backdrop);
    font-family: "Didact Gothic", "Century Gothic", sans-serif;
  }
  .canvas { position: relative; width: 1200px; height: 716px; }
  .card {
    position: absolute; top: 215px;
    width: 500px; height: 286px;
    box-shadow: 0 6px 18px rgba(0,0,0,0.18);
  }
  .card-back {
    left: 70px; background: var(--card-back);
    display: flex; flex-direction: column; align-items: center; justify-content: center;
  }
  .card-back .brand-name {
    color: var(--back-ink); font-size: 32px; letter-spacing: 0.5px; line-height: 1;
  }
  .card-back .tagline {
    color: var(--back-ink-soft); font-size: 14px; letter-spacing: 1px; margin-top: 12px;
  }
  .card-front { left: 630px; background: var(--card-white); }
  .brand-mark {
    position: absolute; left: 58px; top: 64px;
    width: 96px; height: 96px; border-radius: 50%;
    background: var(--leaf-green);
  }
  .identity { position: absolute; left: 186px; top: 58px; }
  .identity .brand-name {
    color: var(--brand-green); font-size: 29px; line-height: 1;
  }
  .identity .person-name {
    color: var(--ink); font-size: 15px; margin-top: 8px; line-height: 1.1;
  }
  .identity .title {
    color: var(--ink-soft); font-size: 11px; margin-top: 3px;
  }
  .contact-list {
    position: absolute; left: 186px; top: 150px;
    list-style: none; color: var(--ink); font-size: 15px;
  }
  .contact-list li {
    display: flex; align-items: center; height: 21px; white-space: nowrap;
  }
  .contact-list li.address { display: block; line-height: 21px; }
  .contact-list svg {
    width: 12px; height: 12px; margin-right: 10px; flex: none;
  }
</style>
</head>
<body>
<main class="canvas">
  <section class="card card-back" aria-label="Card back">
    <span class="brand-name">Petal Quarry</span>
    <span class="tagline">The Professional Salon Source</span>
  </section>

  <section class="card card-front" aria-label="Card front">
    <div class="brand-mark"></div>
    <div class="identity">
      <div class="brand-name">Petal Quarry</div>
      <div class="person-name">Dov Strommen</div>
      <div class="title">President &amp; CEO</div>
    </div>
    <ul class="contact-list">
      <li>
        <svg viewBox="0 0 12 12" aria-hidden="true"><path d="M1 4 Q6 0 11 4 L9 5 L8 3.5 Q6 3 4 3.5 L3 5 Z M2.5 6 H9.5 V11 H2.5 Z" fill="var(--brand-green)"/></svg>
        800-463-5918
      </li>
      <li>
        <svg viewBox="0 0 12 12" aria-hidden="true"><rect x="0.5" y="2" width="11" height="8" fill="none" stroke="var(--brand-green)" stroke-width="1.2"/><path d="M0.5 2 L6 7 L11.5 2" fill="none" stroke="var(--brand-green)" stroke-width="1.2"/></svg>
        dovstrommen@petalquarry.example
      </li>
      <li>
        <svg viewBox="0 0 12 12" aria-hidden="true"><circle cx="6" cy="6" r="5.2" fill="none" stroke="var(--brand-green)" stroke-width="1.2"/><ellipse cx="6" cy="6" rx="2.2" ry="5.2" fill="none" stroke="var(--brand-green)" stroke-width="1"/><path d="M0.8 6 H11.2" stroke="var(--brand-green)" stroke-width="1"/></svg>
        www.petalquarry.example
      </li>
      <li class="address">31 Harlow Ln, Bexmoor, NJ 07813</li>
    </ul>
  </section>
</main>
</body>
</html>
```